Design Website Templates for Photographers for Lumera Inc. (trylumera.example)

Lumera Inc. is a generative website company for wedding photographers.
We are seeking new photography website design inspirations for the next template to be offered on our platform. The catch is you must use the same data for your designs. You also must use all of the data somewhere in the design. You cannot add new content besides the data available. If you wish to add any elements It will be hardcoded and must be universally fitting for many different photographers. We recommend not using any hardcoded test.
Don't be afraid to be creative! Although the most important element of a photographers website is the photos, we are looking for unique and out-of-the-box designs for the actual site as well.
Here is the User generated data available to you:
- 4 Hero Images Landscape, 4 Hero Images Portrait
- Tagline “destination photographer based in Maui, Hawaii”
- “About Photo” of the photographer
- “About” Biography Text
- The design can use up to 3 colors + background color and 2 fonts
- 9 Gallery images
- 3 Packages/services that include landscape/portrait images, a price, a title and text
- Testimonials made up of an image, text and text for the name of testimonial giver
See some examples of our current website designs attached. You can use any of the data you see in the designs.
Updates
We are looking for designs that are less feminine and are more neutral in color and fonts. Currently our templates are more oriented towards feminine photographers. We want to have designs that speak to diverse audiences. We thank everyone for submitting and are reviewing the designs.
Number of Pages Required
1 page
Look and feel
Each slider illustrates characteristics of the customer's brand and the style your logo design should communicate.

```html
<!DOCTYPE html>
<html lang="en">
<head>
<meta charset="utf-8">
<title>Lumera — Destination Photographer</title>
<link rel="stylesheet" href="https://fonts.googleapis.com/css2?family=Raleway:wght@300;400;500;600&family=Open+Sans:wght@400;600&display=swap">
<style>
:root{
  --accent:#f2a81d;
  --ink:#1f1f1f;
  --body:#6f6f6f;
  --line:#9a9a9a;
  --white:#ffffff;
  --footer:#8c8c8c;
  --footer-dark:#1e1e1e;
  --head:"Raleway",sans-serif;
  --text:"Open Sans",sans-serif;
}
*{margin:0;padding:0;box-sizing:border-box}
html,body{width:1200px;height:3938px;overflow:hidden;background:var(--white)}
body{position:relative;font-family:var(--text);color:var(--ink)}
.abs{position:absolute}
.photo{position:absolute}

/* Hero */
.hero{position:absolute;left:0;top:0;width:1200px;height:584px;background:linear-gradient(135deg,#4a3a2e 0%,#6b5444 30%,#8c7a6c 55%,#3d3630 80%,#5b5046 100%)}
.navbar{position:absolute;left:0;top:0;width:1200px;height:57px;background:rgba(0,0,0,.35)}
.brand{position:absolute;left:58px;top:11px;font-family:var(--head);font-weight:500;font-size:30px;letter-spacing:2px;color:var(--white)}
.nav a{position:absolute;top:20px;font-family:var(--head);font-size:12px;font-weight:500;color:var(--white);text-decoration:none;text-transform:uppercase}
.nav a.active{color:var(--accent);border-bottom:1px solid var(--accent);padding-bottom:4px}
.social-label{position:absolute;left:998px;top:7px;font-family:var(--head);font-size:12px;color:var(--accent)}
.social{position:absolute;top:28px}
.social-divider{position:absolute;top:28px;width:1px;height:20px;background:rgba(255,255,255,.5)}
.hero-sub{position:absolute;left:0;width:1200px;top:250px;text-align:center;font-family:var(--head);font-weight:300;font-size:27px;color:var(--white)}
.hero-title{position:absolute;left:0;width:1200px;top:283px;text-align:center;font-family:var(--head);font-weight:500;font-size:53px;color:var(--white)}
.hero-btn{position:absolute;left:514px;top:403px;width:172px;height:31px;border:1px solid var(--white);color:var(--white);font-family:var(--head);font-size:13px;display:flex;align-items:center;justify-content:center;text-transform:uppercase}

/* Welcome */
.welcome-title{position:absolute;left:360px;top:648px;width:340px;text-align:center;font-family:var(--head);font-weight:300;font-size:26px;letter-spacing:.62em;color:#555}
.welcome-text{position:absolute;left:57px;top:727px;width:465px;font-size:12.5px;line-height:19px;color:var(--body)}
.welcome-text p{margin-bottom:19px}
.btn-outline{position:absolute;border:1px solid var(--accent);color:var(--accent);font-size:12.5px;display:flex;align-items:center;justify-content:center;background:var(--white)}
.about-frame{position:absolute;left:821px;top:634px;width:332px;height:403px;background:var(--white)}

/* Section heads */
.section-title{position:absolute;left:0;width:1200px;text-align:center;font-family:var(--head);font-weight:500;font-size:28px;color:var(--ink);text-transform:uppercase}
.rule{position:absolute;height:1px;width:60px;background:var(--accent)}
.section-sub{position:absolute;left:0;width:1200px;text-align:center;font-size:12.5px;color:var(--body)}

/* Services */
.service{position:absolute;top:1936px;width:284px}
.service-photo{width:284px;height:316px}
.service-price{margin-top:22px;font-size:14px;font-weight:600;color:var(--ink)}
.service-price span{font-weight:400;color:var(--accent);margin-left:6px}
.service-name{margin-top:4px;font-size:15.5px;font-weight:600;color:var(--ink)}
.service-text{margin-top:8px;font-size:12.5px;line-height:19.4px;color:var(--body)}
.service .btn-outline{position:static;width:103px;height:31px;margin-top:18px}

/* Testimonials */
.love{position:absolute;left:0;top:2531px;width:1200px;height:316px;background:linear-gradient(180deg,#2a1d10 0%,#5a3a14 35%,#9a6218 60%,#3a2510 85%,#1a120a 100%)}
.love-title{position:absolute;left:0;top:2569px;width:1200px;text-align:center;font-family:var(--head);font-weight:500;font-size:29px;color:var(--white);text-transform:uppercase}
.love-sub{position:absolute;left:0;top:2632px;width:1200px;text-align:center;font-size:13px;color:var(--white)}
.love-quote{position:absolute;left:200px;top:2677px;width:800px;text-align:center;font-size:13px;line-height:25px;color:var(--white)}
.qmark{position:absolute;font-family:var(--head);font-size:38px;font-style:normal;color:var(--white)}
.love-avatar{position:absolute;left:586px;top:2762px;width:27px;height:27px;border-radius:50%;background:linear-gradient(135deg,#cfcfcf,#7a8a9a)}
.love-name{position:absolute;left:0;top:2797px;width:1200px;text-align:center;font-size:13px;font-weight:600;color:var(--white);text-transform:uppercase}

/* Contact */
.connect-title{position:absolute;left:184px;top:2936px;font-family:var(--head);font-weight:500;font-size:29px;color:var(--ink);text-transform:uppercase}
.connect-sub{position:absolute;left:184px;top:3008px;font-size:12.5px;color:var(--body)}
.field{position:absolute;left:184px;width:380px;border:1px solid var(--line);font-size:12.5px;color:var(--body);padding:8px 8px}
.arch{position:absolute;left:624px;top:2897px;width:391px;height:406px;border-radius:196px 196px 0 0;background:linear-gradient(180deg,#6e6a3e 0%,#8a7f56 40%,#c9c4b8 75%,#e8e6e2 100%)}

/* Strip */
.strip-tile{position:absolute;top:3359px;width:299px;height:326px}
.strip-mark{position:absolute;width:18px;height:18px;border:2px solid var(--accent);border-radius:4px}

/* Footer */
.footer{position:absolute;left:0;top:3708px;width:1200px;height:188px;background:var(--footer)}
.footer-head{position:absolute;font-family:var(--head);font-weight:600;font-size:16px;color:var(--accent)}
.footer-link{position:absolute;font-size:12px;color:var(--white)}
.footer-divider{position:absolute;width:1px;background:var(--accent)}
.footer-bar{position:absolute;left:0;top:3896px;width:1200px;height:42px;background:var(--footer-dark);color:var(--white);font-size:12px}
.footer-bar .copy{position:absolute;left:58px;top:14px}
.footer-bar .legal{position:absolute;right:58px;top:14px;word-spacing:2px}
</style>
</head>
<body>

<header class="hero" role="img" aria-label="Wedding couple in formal attire standing in front of a traditional wooden building with blossoms"></header>
<nav class="navbar">
  <div class="brand">LUMERA</div>
  <div class="nav">
    <a class="active" style="left:330px" href="#">About</a>
    <a style="left:432px" href="#">Portfolio</a>
    <a style="left:556px" href="#">Blog</a>
    <a style="left:645px" href="#">Client Love</a>
    <a style="left:780px" href="#">Get in Touch</a>
  </div>
  <div class="social-label">Find me on the internet:</div>
  <svg class="social" style="left:996px" width="14" height="14"><circle cx="7" cy="7" r="6" fill="none" stroke="#fff" stroke-width="1.5"/></svg>
  <div class="social-divider" style="left:1028px;top:25px"></div>
  <svg class="social" style="left:1051px" width="14" height="14"><rect x="1" y="1" width="12" height="12" rx="3" fill="none" stroke="#fff" stroke-width="1.5"/></svg>
  <div class="social-divider" style="left:1087px;top:25px"></div>
  <svg class="social" style="left:1108px" width="20" height="14"><rect x="1" y="1" width="18" height="12" rx="3" fill="none" stroke="#fff" stroke-width="1.5"/></svg>
</nav>
<div class="hero-sub">Destination Photographer</div>
<div class="hero-title">based in Maui, Hawaii</div>
<svg class="abs" style="left:594px;top:355px" width="12" height="38"><line x1="6" y1="0" x2="6" y2="36" stroke="#fff" stroke-width="1"/><polyline points="2,31 6,36 10,31" fill="none" stroke="#fff" stroke-width="1"/></svg>
<div class="hero-btn">Book with me</div>

<!-- Welcome -->
<section>
  <h2 class="welcome-title">WELCOME</h2>
  <div class="welcome-text">
    <p>Hi and welcome to Lumera Inc. Photography, this is a place where I hope you get to know little about me and decide for yourself we can work well together and maybe become a friend.</p>
    <p>You will learn about me the most by visiting About section where I explain why I do what I do and what I hope to achieve photographing your day.</p>
    <p>If you can only visit one page on this entire website, I would kindly point you to Blog. The blog is my journal, my recommendations of being a wedding expert and where you will see the photos of the entire day rather than only my best or my favourite photos.</p>
    <p>I hope you enjoy and I hope we will connect, but if we don't, I wish you the best in finding an amazing photographer who is going to be perfect for an absolutely beautiful day of your life.</p>
  </div>
  <div class="btn-outline" style="left:57px;top:1032px;width:102px;height:31px">Read More</div>
  <div class="photo" style="left:560px;top:694px;width:330px;height:401px;background:linear-gradient(160deg,#3a4a2e,#2b3524 50%,#4a5a3a)" role="img" aria-label="Aerial view of a couple lying on a garden path"></div>
  <div class="about-frame"></div>
  <div class="photo" style="left:829px;top:642px;width:316px;height:387px;background:linear-gradient(160deg,#a8a59c,#8e8f8c 50%,#c7c4c0)" role="img" aria-label="About photo: couple embracing with a bouquet"></div>
</section>

<!-- Gallery -->
<section aria-label="Gallery">
  <div class="photo" style="left:40px;top:1151px;width:272px;height:399px;background:linear-gradient(170deg,#5a5552,#c9c2ba 60%,#3f4a3a)" role="img" aria-label="Bride with tattoo holding a white bouquet"></div>
  <div class="photo" style="left:40px;top:1561px;width:272px;height:200px;background:linear-gradient(170deg,#c8b8a4,#8a7a6a)" role="img" aria-label="Close-up of a bride's hands on her dress"></div>
  <div class="photo" style="left:323px;top:1151px;width:272px;height:199px;background:linear-gradient(170deg,#5a6a8a,#3a4a2a 60%,#2a3a5a)" role="img" aria-label="Couple kissing under a floral arch by a lake"></div>
  <div class="photo" style="left:323px;top:1361px;width:272px;height:400px;background:linear-gradient(170deg,#9ab08a,#e6ddd2 55%,#b8a898)" role="img" aria-label="Bride holding a pastel bouquet among blossoms"></div>
  <div class="photo" style="left:605px;top:1151px;width:273px;height:399px;background:linear-gradient(170deg,#b8b8b4,#3a4458 55%,#d8d6d2)" role="img" aria-label="Groom and bride leaning close with a bouquet"></div>
  <div class="photo" style="left:605px;top:1561px;width:273px;height:200px;background:linear-gradient(170deg,#3a3632,#d6c6ae 60%,#8a6a3a)" role="img" aria-label="Couple holding hands with dried flowers"></div>
  <div class="photo" style="left:888px;top:1151px;width:271px;height:199px;background:linear-gradient(170deg,#d22a1e,#e24a32 60%,#a81a14)" role="img" aria-label="Portrait with a red floral headpiece"></div>
  <div class="photo" style="left:888px;top:1361px;width:271px;height:400px;background:linear-gradient(170deg,#d8d2b8,#b8b488 50%,#e8e2d2)" role="img" aria-label="Bride in a field holding a bouquet"></div>
</section>

<!-- Services -->
<section>
  <h2 class="section-title" style="top:1806px">Photography Services</h2>
  <div class="rule" style="left:570px;top:1853px"></div>
  <p class="section-sub" style="top:1870px">These are a few of my most popular photography services. Take a look!</p>

  <article class="service" style="left:128px">
    <div class="service-photo" style="background:linear-gradient(180deg,#6a7868,#3a4a2a 50%,#4a4a3a)" role="img" aria-label="Temple gate at the end of a long path"></div>
    <div class="service-price">Price: <span>$253</span></div>
    <h3 class="service-name">Adventure Elopements</h3>
    <p class="service-text">Do you have slightly different wedding idea than some of your friends and families? You love them, but maybe you want the day to be just you two doing things you love, hiking, camping, strolling on a beach, stargazing or whatever it may be, this option is for you.</p>
    <div class="btn-outline">Read More</div>
  </article>

  <article class="service" style="left:457px">
    <div class="service-photo" style="background:linear-gradient(180deg,#a8a898,#7a8468 50%,#d8d4cc)" role="img" aria-label="Couple in a birch forest holding a bouquet"></div>
    <div class="service-price">Price: <span>$453</span></div>
    <h3 class="service-name">Traditional Weddings</h3>
    <p class="service-text">You have been waiting for the pandemic to be over so that you can see everyone at your wedding and just party all night long after getting married at one of your dream venue. Let's get you married.</p>
    <div class="btn-outline">Read More</div>
  </article>

  <article class="service" style="left:787px">
    <div class="service-photo" style="background:linear-gradient(180deg,#3a1e08,#a85a10 45%,#e0901e 60%,#1a0e04)" role="img" aria-label="Couple silhouetted against a sunset"></div>
    <div class="service-price">Price: <span>$353</span></div>
    <h3 class="service-name">Engagements &amp; Honeymoon</h3>
    <p class="service-text">Combining a couple photography session with travel has always been the sweet harmony for Reid Cole Photography and we got to do a lot of these, over 300 couples in four years to be a bit more precise. So wherever you go, if you wish I would love to tag along.</p>
    <div class="btn-outline">Read More</div>
  </article>
</section>

<!-- Client love -->
<section>
  <div class="love" role="img" aria-label="Couple silhouetted on a hill at dusk"></div>
  <h2 class="love-title">Client Love</h2>
  <div class="rule" style="left:570px;top:2616px"></div>
  <p class="love-sub">Kind words from some of my favourite people.</p>
  <span class="qmark" style="left:191px;top:2660px">“</span>
  <p class="love-quote">We decided to have a destination wedding. The photographs were very important and allowed us to share the experience with family once we returned home. Best photographer ever. Amazing photographer, very professional, and fit in great with our wedding party. Reid not only captured our ceremony but rode around Vegas to photograph many locations.</p>
  <span class="qmark" style="left:916px;top:2722px">”</span>
  <div class="love-avatar" role="img" aria-label="Client portrait"></div>
  <div class="love-name">Marisol + Devin</div>
  <svg class="abs" style="left:62px;top:2700px" width="14" height="20"><polyline points="11,2 3,10 11,18" fill="none" stroke="#fff" stroke-width="1.5"/></svg>
  <svg class="abs" style="left:1130px;top:2700px" width="14" height="20"><polyline points="3,2 11,10 3,18" fill="none" stroke="#fff" stroke-width="1.5"/></svg>
</section>

<!-- Contact -->
<section>
  <h2 class="connect-title">Lets Connect</h2>
  <div class="rule" style="left:184px;top:2989px;width:70px"></div>
  <p class="connect-sub">It is a long established fact that a reader will be</p>
  <div class="field" style="top:3047px;height:36px">full name:</div>
  <div class="field" style="top:3090px;height:35px">Email Address:</div>
  <div class="field" style="top:3133px;height:35px">Phone Number</div>
  <div class="field" style="top:3177px;height:78px">Tell Me About Yourself</div>
  <div class="btn-outline" style="left:184px;top:3274px;width:103px;height:29px;text-transform:uppercase">Submit</div>
  <div class="arch" role="img" aria-label="Couple standing hand in hand under trees"></div>
</section>

<!-- Photo strip -->
<section aria-label="Recent photos">
  <div class="strip-tile" style="left:0;background:linear-gradient(160deg,#e88a10,#c86a08 60%,#8a4a0a)" role="img" aria-label="Couple seated on rocks in golden light"></div>
  <div class="strip-tile" style="left:301px;background:linear-gradient(160deg,#5a6a6a,#d8d8d4 55%,#3a3a3a)" role="img" aria-label="Couple in white at a table with flowers"></div>
  <div class="strip-tile" style="left:602px;background:linear-gradient(160deg,#2a1a1a,#6a3a3a 55%,#1e1414)" role="img" aria-label="Couple kissing in low light"></div>
  <div class="strip-tile" style="left:902px;background:linear-gradient(160deg,#7a6a10,#4a4212 55%,#2a2410)" role="img" aria-label="Couple walking hand in hand at dusk"></div>
  <div class="strip-mark" style="left:268px;top:3654px"></div>
  <div class="strip-mark" style="left:568px;top:3654px"></div>
  <div class="strip-mark" style="left:869px;top:3654px"></div>
  <div class="strip-mark" style="left:1170px;top:3654px"></div>
</section>

<!-- Footer -->
<footer>
  <div class="footer"></div>
  <div class="footer-head" style="left:57px;top:3731px">Book a Photographer</div>
  <div class="footer-link" style="left:57px;top:3776px">Marketplace</div>
  <div class="footer-link" style="left:57px;top:3801px">How it Works</div>
  <div class="footer-link" style="left:57px;top:3825px">About</div>
  <div class="footer-link" style="left:57px;top:3851px">Blog</div>
  <div class="footer-link" style="left:216px;top:3776px">FAQ</div>
  <div class="footer-link" style="left:216px;top:3801px">Terms of Service</div>
  <div class="footer-divider" style="left:394px;top:3786px;height:105px"></div>

  <div class="footer-head" style="left:471px;top:3728px">For Photographers</div>
  <div class="footer-link" style="left:471px;top:3773px">Login</div>
  <div class="footer-link" style="left:471px;top:3798px">Pricing</div>
  <div class="footer-link" style="left:471px;top:3822px">Knowledge base</div>
  <div class="footer-link" style="left:471px;top:3847px">Free mentorship</div>
  <div class="footer-link" style="left:471px;top:3872px">Blog</div>
  <div class="footer-link" style="left:630px;top:3773px">FAQ</div>
  <div class="footer-link" style="left:630px;top:3798px">Policies</div>
  <div class="footer-link" style="left:630px;top:3822px">Terms of Service</div>
  <div class="footer-divider" style="left:810px;top:3786px;height:80px"></div>

  <div class="footer-head" style="left:893px;top:3731px">Contact Info</div>
  <svg class="abs" style="left:895px;top:3771px" width="16" height="16"><path d="M3 1 L6 1 L7.5 5 L5.5 6.5 Q7 10 9.5 10.5 L11 8.5 L15 10 L15 13 Q14 15 11 14.5 Q3 12 1.5 4 Q1.5 1.5 3 1 Z" fill="none" stroke="var(--accent)" stroke-width="1.2"/></svg>
  <div class="footer-link" style="left:931px;top:3772px">+1 555 014 2270</div>
  <svg class="abs" style="left:894px;top:3806px" width="18" height="13"><rect x="1" y="1" width="16" height="11" fill="none" stroke="var(--accent)" stroke-width="1.2"/><polyline points="1,1 9,7 17,1" fill="none" stroke="var(--accent)" stroke-width="1.2"/></svg>
  <div class="footer-link" style="left:931px;top:3805px">mailto:contact@trylumera.example</div>
  <svg class="abs" style="left:896px;top:3836px" width="14" height="19"><path d="M7 18 Q1 10 1 7 A6 6 0 0 1 13 7 Q13 10 7 18 Z" fill="none" stroke="var(--accent)" stroke-width="1.2"/><circle cx="7" cy="7" r="2.2" fill="none" stroke="var(--accent)" stroke-width="1.2"/></svg>
  <div class="footer-link" style="left:931px;top:3840px">240 Harbour Lane, Victoria, BC V8V 0A1</div>

  <div class="footer-bar">
    <span class="copy">©2023 Lumera</span>
    <span class="legal">Meet Me &nbsp; | &nbsp; Photos &nbsp; | &nbsp; Associates &nbsp; | &nbsp; Film</span>
  </div>
</footer>

</body>
</html>
```